Friendly website/webshop needed for small family store

Hello .. I really need a website that is easy to use as I have no experience with this at all. ..
My shop is called quillmoss and I had a fantastic logo from craft forge - I asked for something mid century modern and I love it. I will attach . There might be some development around the logo now for various paraphernalia ( stickers , printed tissue paper carrier bags etc.. ) I would also like some sort of help with a slogan such as 'sing your prettiest song' as in,  live your best life etc..  but I'm not sure if this is a little trite .... ? but it would be nice to link the quillmoss with a little Motto.    If I need to pay extra for this - please could you let me know ... I'm happy to add on payment ..
As you can see the only LOGO colours really are grey black and orange .. so I would like some ideas to expand on the bird  to bring in some more colours.....  the tag line flower.children.home I would like to drop..
* the original brief included flowers on the tag line  because at the time we were also a florist . we now just sell dried flowers
My shop is in the beautiful town of Malvern, we have lots of tourist that come to walk the hills and enjoy nature - it's a family and dog friendly sort of town and we are a dog and family friendly sort of shop :-) It's a relaxed space that focuses on beautiful handmade items such as baskets & wooden utensils  from Africa, textiles from India and ceramics from France, Portugal and Italy.  We have a lovely section for children that sells beautiful soft toys from Charmel Duvo and the wonderful mice family and bunnies from Tornby.
We stock OBRETI homeware which is lovely and earthy and natural.
We would like to communicate the value of buying thoughtfully  and conscientiously, of building a beautiful home whilst investing in & supporting makers world wide. We don't sell anything that can't be repurposed, recycled etc..
Thank you

```html
<!DOCTYPE html>
<html lang="en">
<head>
<meta charset="utf-8">
<title>quillmoss — sing your prettiest song</title>
<link href="https://fonts.googleapis.com/css2?family=Comfortaa:wght@500;700&family=Jost:wght@400;500;600&display=swap" rel="stylesheet">
<style>
:root{
  --salmon:#c98473;
  --salmon-dark:#a9675a;
  --teal:#6ea9b7;
  --teal-soft:#a9cdd6;
  --ink:#1b1b1b;
  --text:#3c3c3c;
  --muted:#777;
  --paper:#ffffff;
  --footer:#111111;
}
*{box-sizing:border-box;margin:0;padding:0}
html,body{width:1200px;height:3888px;overflow:hidden;background:var(--paper)}
body{font-family:"Jost",sans-serif;color:var(--text);position:relative}
.display{font-family:"Comfortaa",sans-serif}
.abs{position:absolute}
.btn{display:inline-block;font-family:"Jost",sans-serif;color:#fff;font-size:18px;padding:10px 26px;border-radius:3px;background:var(--salmon);white-space:nowrap}
.btn.teal{background:var(--teal)}

/* header */
.topbar{left:560px;top:0;width:640px;height:56px;background:var(--salmon);display:flex;align-items:center;justify-content:space-around;color:#fff;font-size:15px;padding:0 20px 0 40px;clip-path:polygon(4% 0,100% 0,100% 100%,0 100%)}
.topbar span{white-space:nowrap}
.topbar span::before{content:"";display:inline-block;width:12px;height:12px;border-radius:50%;background:#fff;margin-right:8px;vertical-align:-1px;opacity:.85}
.brand{left:96px;top:14px;width:280px}
.brand-row{display:flex;align-items:center;gap:12px}
.brand-dot{width:44px;height:44px;border-radius:50%;background:var(--salmon)}
.brand-name{font-family:"Comfortaa",sans-serif;font-weight:700;font-size:40px;color:var(--ink)}
.brand-tag{font-family:"Jost",sans-serif;font-size:15px;color:var(--teal);margin:4px 0 0 56px}
.nav{left:380px;top:90px;display:flex;gap:46px;align-items:center;font-size:18px;color:var(--ink);font-weight:500}
.nav .active{border-bottom:2px solid var(--teal);padding-bottom:4px}
.nav .btn{margin-left:30px;background:var(--teal);font-size:17px;padding:8px 24px}

/* hero */
.hero{left:0;top:152px;width:1200px;height:648px;background:linear-gradient(180deg,#5b4a3a 0%,#6d5a45 40%,#4a3c30 100%)}
.hero-shade{position:absolute;inset:0;background:rgba(20,15,10,.35)}
.hero-copy{position:absolute;left:0;right:0;top:215px;text-align:center;color:#fff}
.hero-copy .welcome{font-family:"Comfortaa",sans-serif;font-size:40px;font-weight:700}
.hero-copy h1{font-family:"Comfortaa",sans-serif;font-size:110px;font-weight:700;line-height:1.1}
.hero-copy .slogan{font-family:"Comfortaa",sans-serif;font-size:30px;font-weight:700;margin-top:2px}
.hero-copy .btn{margin-top:30px;font-size:17px;padding:8px 22px}

/* about */
.about-title{left:112px;top:885px;font-size:56px;color:var(--ink);font-weight:700}
.about-text{left:112px;top:975px;width:490px;font-size:17px;line-height:1.7;color:var(--text)}
.about-btn{left:112px;top:1212px;font-size:17px;padding:8px 24px}
.about-photo{top:888px;height:372px;background:linear-gradient(160deg,#8a7a66,#5b4c3e)}
.about-photo.one{left:632px;width:262px}
.about-photo.two{left:900px;width:292px;background:linear-gradient(180deg,#5c5e64,#2c2f33 55%,#7a7a78)}

/* products */
.products-band{left:0;top:1340px;width:1200px;height:650px}
.products-title{left:0;width:1200px;top:1450px;text-align:center;font-size:48px;color:#fff;font-weight:700}
.card{top:1578px;width:312px;height:272px;background:#fff;border-radius:6px;box-shadow:0 6px 18px rgba(0,0,0,.12);overflow:hidden}
.card .photo{position:absolute;left:16px;top:16px;width:280px;height:168px;border-radius:4px}
.card .name{position:absolute;left:20px;top:212px;font-family:"Comfortaa",sans-serif;font-weight:700;font-size:24px;color:var(--ink)}
.card .btn{position:absolute;right:16px;top:206px;font-size:16px;padding:7px 18px}
.arrow{top:1712px;width:40px;height:40px;border-radius:50%;background:#fff;display:flex;align-items:center;justify-content:center;box-shadow:0 2px 8px rgba(0,0,0,.15)}

/* testimonial */
.testi-card{left:112px;top:2090px;width:976px;height:390px;background:#fff;border-radius:8px;box-shadow:0 4px 24px rgba(0,0,0,.14);text-align:center}
.testi-card h2{margin-top:36px;font-size:48px;color:var(--ink);font-weight:700}
.testi-card .quote{font-family:"Comfortaa",sans-serif;font-size:50px;color:var(--ink);line-height:1;margin-top:18px}
.stars{color:#e8a33c;font-size:20px;letter-spacing:4px}
.testi-card p{width:760px;margin:12px auto 0;font-size:19px;line-height:1.55;color:var(--text)}
.testi-card .who{margin-top:26px;font-family:"Comfortaa",sans-serif;font-weight:700;font-size:24px;color:var(--ink)}
.testi-card .role{font-size:16px;color:var(--muted)}
.t-arrow{top:2310px;width:38px;height:38px;border-radius:50%;background:#e6e6e6;display:flex;align-items:center;justify-content:center}
.avatar{border-radius:50%;border:3px solid #fff;box-shadow:0 2px 8px rgba(0,0,0,.2)}

/* facts */
.facts{left:0;top:2700px;width:1200px;height:370px}
.facts-title{left:112px;top:2830px;font-family:"Comfortaa",sans-serif;font-weight:700;font-size:44px;line-height:1.2;color:#fff}
.fact{top:2835px;color:#fff;font-size:24px;line-height:1.35;font-weight:500}
.fact-rule{top:2830px;width:2px;height:110px;background:rgba(255,255,255,.8)}

/* contact */
.contact-title{left:0;width:1200px;top:3120px;text-align:center;font-size:46px;color:var(--ink);font-weight:700}
.field{height:64px;border:1px solid #ddd;border-radius:3px;box-shadow:0 2px 6px rgba(0,0,0,.08);font-size:15px;color:#888;padding:18px 20px;background:#fff}
.submit{left:112px;top:3366px;width:632px;height:58px;background:var(--teal);color:#fff;font-size:18px;font-weight:500;display:flex;align-items:center;justify-content:center;border-radius:3px}

/* footer */
.footer{left:0;top:3508px;width:1200px;height:340px;background:var(--footer);color:#fff}
.footer h4{font-size:20px;font-weight:500;margin-bottom:22px}
.footer ul{list-style:none;font-size:15px;line-height:1.75}
.socials{display:flex;gap:10px}
.socials span{width:22px;height:22px;background:#fff;border-radius:3px}
.info-row{display:flex;align-items:center;gap:18px;font-size:15px;margin-bottom:22px;white-space:nowrap}
.info-row i{width:34px;height:34px;border-radius:50%;background:#fff;display:flex;align-items:center;justify-content:center;flex:none}
.copyright{left:0;top:3848px;width:1200px;height:40px;background:#000;color:#ddd;font-size:14px;display:flex;align-items:center;justify-content:center}
</style>
</head>
<body>

<!-- header -->
<div class="abs topbar"><span>14 Fernhill Lane, Malvern</span><span>01632960481</span><span>www.quillmoss-shop.com</span></div>
<div class="abs brand">
  <div class="brand-row"><div class="brand-dot"></div><div class="brand-name">quillmoss</div></div>
  <div class="brand-tag">sing your prettiest song</div>
</div>
<nav class="abs nav">
  <span class="active">Home</span><span>About Us</span><span>Products</span><span>Testimonials</span><span>Blog</span>
  <span class="btn">Contact Us</span>
</nav>

<!-- hero -->
<section class="abs hero" role="img" aria-label="Interior of the shop with baskets, textiles and homeware on shelves">
  <div class="hero-shade"></div>
  <div class="hero-copy">
    <div class="welcome">Welcome to</div>
    <h1>quillmoss</h1>
    <div class="slogan">sing your prettiest song</div>
    <span class="btn">Get Started</span>
  </div>
</section>

<!-- about -->
<h2 class="abs about-title display">About Us</h2>
<p class="abs about-text">Sed ut perspiciatis unde omnis iste natus error sit voluptatem accusantium doloremque laudantium, totam rem aperiam, eaque ipsa quae ab illo inventore veritatis et quasi architecto beatae vitae dicta sunt explicabo. Nemo enim ipsam voluptatem quia voluptas sit aspernatur aut odit aut fugit, sed quia consequuntur magni dolores eos qui ratione voluptatem sequi nesciunt.</p>
<span class="abs btn teal about-btn">Read More</span>
<div class="abs about-photo one" role="img" aria-label="Handmade homeware displayed on a wooden table"></div>
<div class="abs about-photo two" role="img" aria-label="Shop front on a town street"></div>

<!-- products -->
<svg class="abs products-band" viewBox="0 0 1200 650" aria-hidden="true">
  <defs><linearGradient id="bandGrad" x1="0" y1="0" x2="1" y2="1"><stop offset="0" stop-color="#7fb4c1"/><stop offset="1" stop-color="#5e98a7"/></linearGradient></defs>
  <polygon points="0,0 1200,90 1200,560 0,650" fill="url(#bandGrad)"/>
</svg>
<h2 class="abs products-title display">Our Products</h2>
<div class="abs card" style="left:108px">
  <div class="photo" role="img" aria-label="Photo of a woven wicker basket" style="background:linear-gradient(180deg,#f4ece4,#e2c9a8)"></div>
  <div class="name">Baskets</div><span class="btn">View More</span>
</div>
<div class="abs card" style="left:440px">
  <div class="photo" role="img" aria-label="Photo of a carved wooden bowl" style="background:linear-gradient(180deg,#f5eee8,#e6c4a4)"></div>
  <div class="name">Wooden</div><span class="btn">View More</span>
</div>
<div class="abs card" style="left:772px">
  <div class="photo" role="img" aria-label="Photo of a painted ceramic vase" style="background:linear-gradient(180deg,#f6eeec,#e3b8ae)"></div>
  <div class="name">Ceramics</div><span class="btn">View More</span>
</div>
<div class="abs arrow" style="left:36px"><svg width="14" height="14" viewBox="0 0 14 14"><path d="M9 2 L4 7 L9 12" stroke="#555" stroke-width="2" fill="none"/></svg></div>
<div class="abs arrow" style="left:1128px"><svg width="14" height="14" viewBox="0 0 14 14"><path d="M5 2 L10 7 L5 12" stroke="#555" stroke-width="2" fill="none"/></svg></div>

<!-- testimonial -->
<svg class="abs" style="left:112px;top:2380px" width="976" height="240" viewBox="0 0 976 240" aria-hidden="true">
  <path d="M40 0 Q488 300 936 0" stroke="var(--teal)" stroke-width="3" fill="none"/>
</svg>
<div class="abs testi-card">
  <h2 class="display">What Our Client Changes?</h2>
  <div class="quote">“</div>
  <div class="stars">★★★★★</div>
  <p>Lorem ipsum dolor sit amet, consectetur adipisicing elit, sed do eiusmod tempor incididunt ut labore et dolore magna aliqua. Ut enim ad minim veniam, quis nostrud exercitation ullamco laboris nisi ut aliquip ex ea commodo consequat.</p>
  <div class="who">Marla Fennick</div>
  <div class="role">Manager</div>
</div>
<div class="abs t-arrow" style="left:93px"><svg width="12" height="12" viewBox="0 0 12 12"><path d="M8 1 L3 6 L8 11" stroke="#888" stroke-width="2" fill="none"/></svg></div>
<div class="abs t-arrow" style="left:1069px"><svg width="12" height="12" viewBox="0 0 12 12"><path d="M4 1 L9 6 L4 11" stroke="#888" stroke-width="2" fill="none"/></svg></div>
<div class="abs avatar" role="img" aria-label="Client portrait" style="left:492px;top:2530px;width:56px;height:56px;background:#b49582"></div>
<div class="abs avatar" role="img" aria-label="Client portrait" style="left:566px;top:2518px;width:72px;height:72px;background:#9a7560"></div>
<div class="abs avatar" role="img" aria-label="Client portrait" style="left:656px;top:2530px;width:56px;height:56px;background:#c4a28d"></div>

<!-- facts -->
<svg class="abs facts" viewBox="0 0 1200 370" role="img" aria-label="Baskets and woven goods photographed in warm tones">
  <defs><linearGradient id="factsGrad" x1="0" y1="0" x2="1" y2="0"><stop offset="0" stop-color="#b06e5f"/><stop offset=".5" stop-color="#c4887a"/><stop offset="1" stop-color="#a86456"/></linearGradient></defs>
  <path d="M0 40 Q600 -40 1200 40 L1200 370 L0 370 Z" fill="url(#factsGrad)"/>
</svg>
<h3 class="abs facts-title">Some<br>Important<br>Facts</h3>
<div class="abs fact" style="left:440px">5000+<br>Projects<br>Completed</div>
<div class="abs fact-rule" style="left:620px"></div>
<div class="abs fact" style="left:675px">10+<br>Years Of<br>Experience</div>
<div class="abs fact-rule" style="left:875px"></div>
<div class="abs fact" style="left:935px">30+<br>Experience<br>Empoyers</div>

<!-- contact -->
<h2 class="abs contact-title display">Contact Us</h2>
<div class="abs field" style="left:112px;top:3208px;width:310px">Name</div>
<div class="abs field" style="left:434px;top:3208px;width:310px">Email</div>
<div class="abs field" style="left:112px;top:3286px;width:310px">Phone</div>
<div class="abs field" style="left:434px;top:3286px;width:310px">Subject</div>
<div class="abs field" style="left:760px;top:3208px;width:328px;height:142px">Message</div>
<div class="abs submit">Submit Now</div>

<!-- footer -->
<footer class="abs footer">
  <div class="abs" style="left:120px;top:50px">
    <div class="brand-row"><div class="brand-dot" style="width:40px;height:40px"></div><div class="brand-name" style="color:#fff;font-size:36px">quillmoss</div></div>
    <div style="font-size:14px;color:var(--teal);margin:4px 0 30px 52px">sing your prettiest song</div>
    <div class="socials"><span></span><span></span><span></span><span></span></div>
  </div>
  <div class="abs" style="left:400px;top:74px"><h4>Quick Links</h4><ul><li>Home</li><li>About Us</li><li>Products</li><li>Testimonials</li><li>Blog</li><li>Contact Us</li></ul></div>
  <div class="abs" style="left:602px;top:74px"><h4>Other Links</h4><ul><li>Privacy Policy</li><li>Terms &amp; Conditions</li><li>Disclaimer</li></ul></div>
  <div class="abs" style="left:860px;top:74px">
    <h4>Contact Info</h4>
    <div class="info-row"><i><svg width="14" height="16" viewBox="0 0 14 16"><path d="M7 0 C3 0 0 3 0 6.5 C0 11 7 16 7 16 C7 16 14 11 14 6.5 C14 3 11 0 7 0 Z" fill="#111"/><circle cx="7" cy="6.5" r="2.4" fill="#fff"/></svg></i>14 Fernhill Lane, Malvern</div>
    <div class="info-row"><i><svg width="16" height="16" viewBox="0 0 16 16"><path d="M3 1 L6 1 L7 5 L5 6.5 C6 9 7 10 9.5 11 L11 9 L15 10 L15 13 C15 14 14 15 13 15 C6 15 1 10 1 3 C1 2 2 1 3 1 Z" fill="#111"/></svg></i>01632960481</div>
    <div class="info-row"><i><svg width="16" height="16" viewBox="0 0 16 16"><circle cx="8" cy="8" r="6.5" stroke="#111" stroke-width="1.6" fill="none"/><path d="M1.5 8 H14.5 M8 1.5 C5 5 5 11 8 14.5 M8 1.5 C11 5 11 11 8 14.5" stroke="#111" stroke-width="1.3" fill="none"/></svg></i>www.quillmoss-shop.com</div>
  </div>
</footer>
<div class="abs copyright">Copyright © 2024 quillmoss. All rights reserved.</div>

</body>
</html>
```